q-zen design for startup inpection service

building and pest inspections what i had in mind was q-zen in large print with prepurchase in small print directly under it and the small tm (tradmark) .Within the C I would like an eye but I don't want to take away from the C so maybe the eye would be done in a fine line?I would also like the Building and Pest inspections to be prominent and large .Have no idea of colors but do like black orange and silver

Target Market(s)

home buyers and realestate agents

Industry/Entity Type

Building

Contact Information for Business Card

q-zen prepurchase, Phone 0412093816, fax 02 71934058, email q-zen@mailbrook.com.au ,building and pest inspections

Font styles to use
Sans Serif

Requirements
Must have
• bold color
• simple layout
• bold color
• uncluttered layout
Should not have
• contact details the same size as Building and Pest Inspections

```html
<!DOCTYPE html>
<html lang="en">
<head>
<meta charset="utf-8">
<title>q-zen prepurchase — business card</title>
<link rel="stylesheet" href="https://fonts.googleapis.com/css2?family=PT+Serif:wght@400;700&display=swap">
<style>
  :root {
    --page-bg: #e6e4e0;
    --card-white: #fbfbfa;
    --card-shade: #efefed;
    --ink-black: #141414;
    --ink-dark: #2a2a2a;
    --ink-grey: #5c5c5c;
    --rule-grey: #b9b9b9;
    --band-black: #0f0f0f;
    --band-grey: #4a4a4a;
    --band-text: #ffffff;
  }
  * { margin: 0; padding: 0; box-sizing: border-box; }
  html, body {
    width: 1200px;
    height: 818px;
    overflow: hidden;
    background: var(--page-bg);
    font-family: "PT Serif", Georgia, serif;
  }
  .card {
    position: absolute;
    left: 75px;
    top: 109px;
    width: 1050px;
    height: 600px;
    background: linear-gradient(135deg, var(--card-white) 0%, var(--card-shade) 100%);
    box-shadow: 0 6px 24px rgba(0,0,0,0.18);
    overflow: hidden;
  }
  .card__band {
    position: absolute;
    inset: 0;
    width: 1050px;
    height: 600px;
  }
  .services {
    font-family: "PT Serif", Georgia, serif;
    font-size: 32px;
    fill: var(--band-text);
  }
  .brand {
    position: absolute;
    left: 70px;
    top: 190px;
    width: 450px;
    text-align: right;
    color: var(--ink-dark);
  }
  .brand__name {
    display: block;
    font-size: 124px;
    font-weight: 700;
    line-height: 1;
    letter-spacing: 2px;
    text-transform: uppercase;
    padding-bottom: 26px;
  }
  .brand__tagline {
    display: block;
    font-size: 42px;
    font-weight: 400;
    line-height: 1.1;
    letter-spacing: 2px;
    text-transform: uppercase;
    color: var(--ink-grey);
  }
  .divider {
    position: absolute;
    left: 575px;
    top: 100px;
    width: 1px;
    height: 340px;
    background: linear-gradient(to bottom, transparent, var(--rule-grey) 20%, var(--rule-grey) 80%, transparent);
  }
  .person {
    position: absolute;
    left: 625px;
    top: 110px;
  }
  .person__name {
    font-size: 38px;
    font-weight: 700;
    color: var(--ink-black);
    line-height: 1.1;
  }
  .person__role {
    font-size: 27px;
    color: var(--ink-grey);
    line-height: 1.2;
  }
  .contacts {
    position: absolute;
    left: 625px;
    top: 225px;
    list-style: none;
  }
  .contacts__item {
    display: flex;
    align-items: center;
    gap: 18px;
    font-size: 26px;
    color: var(--ink-dark);
    line-height: 42px;
  }
  .contacts__icon {
    width: 22px;
    height: 22px;
    flex: none;
  }
</style>
</head>
<body>
  <div class="card">
    <svg class="card__band" viewBox="0 0 1050 600">
      <defs>
        <linearGradient id="bandFill" x1="0" y1="0" x2="1" y2="0">
          <stop offset="0" stop-color="var(--band-grey)"/>
          <stop offset="0.45" stop-color="var(--band-black)"/>
          <stop offset="1" stop-color="var(--band-black)"/>
        </linearGradient>
        <path id="servicesPath" d="M380 655 C 650 570, 900 515, 1100 410"/>
      </defs>
      <path d="M260 600 C 560 500, 820 440, 1050 330 L1050 600 Z" fill="url(#bandFill)"/>
      <path d="M330 600 C 600 515, 850 460, 1050 355" fill="none" stroke="#ffffff" stroke-width="3"/>
      <text class="services" text-anchor="end">
        <textPath href="#servicesPath" startOffset="88%">building and pest inspections</textPath>
      </text>
    </svg>

    <div class="brand">
      <span class="brand__name">Q-ZEN</span>
      <span class="brand__tagline">Prepurchase</span>
    </div>

    <div class="divider"></div>

    <div class="person">
      <p class="person__name">Employee Name</p>
      <p class="person__role">Managing Director</p>
    </div>

    <ul class="contacts">
      <li class="contacts__item">
        <svg class="contacts__icon" viewBox="0 0 24 24" aria-label="Phone">
          <path d="M6.6 10.8a15 15 0 0 0 6.6 6.6l2.2-2.2a1 1 0 0 1 1-.25 11.4 11.4 0 0 0 3.6.6 1 1 0 0 1 1 1V20a1 1 0 0 1-1 1A17 17 0 0 1 3 4a1 1 0 0 1 1-1h3.5a1 1 0 0 1 1 1c0 1.25.2 2.45.6 3.6a1 1 0 0 1-.25 1z" fill="var(--ink-black)"/>
        </svg>
        <span>0412093816</span>
      </li>
      <li class="contacts__item">
        <svg class="contacts__icon" viewBox="0 0 24 24" aria-label="Fax">
          <rect x="6" y="2" width="12" height="6" fill="var(--ink-black)"/>
          <rect x="2" y="9" width="20" height="9" rx="1.5" fill="var(--ink-black)"/>
          <rect x="6" y="15" width="12" height="7" fill="var(--ink-black)" stroke="var(--card-white)" stroke-width="1.5"/>
        </svg>
        <span>02 71934058</span>
      </li>
      <li class="contacts__item">
        <svg class="contacts__icon" viewBox="0 0 24 24" aria-label="Email">
          <rect x="2" y="5" width="20" height="14" fill="var(--ink-black)"/>
          <path d="M2 5 L12 13 L22 5 M2 19 L9.5 11 M22 19 L14.5 11" fill="none" stroke="var(--card-white)" stroke-width="1.5"/>
        </svg>
        <span>q-zen@mailbrook.com.au</span>
      </li>
    </ul>
  </div>
</body>
</html>
```